ULMIRA card Technical Architecture

Hello everyone ULMIRA: It is a consulting firm in Architecture and Construction. I require a card duplexing, sober, elegant, classic but not boring. Update 1: Use the following data for the card. Name: Gonzalo Pereda Mauricio Villalta Position: COO Twitter: @ulmiraAT Homepage: ulmira-example.com home address not include the participation of all thank you.

Target Market(s)

Construction companies, Architects and Consulting Engineers

Industry/Entity Type

Consulting

Contact Information for Business Card

Los campos que debe tener:
Nombre, Cargo, email, homepage y twitter

Font styles to use
Serif
Sans Serif
Other font styles liked:
• Me gustan playfair display, open sans y roboto, pero estoy sujeto a sus propuestas

Requirements
Must have
• Colors: Present combined proposals in white, red, gray and black Update 1: The two names must be clearly differentiated from the two surnames
Nice to have
• They are free to present their best proposals. I will bring them immediate feedback to the extent you can go see their designs. Complete data for card and logo files will give the winner the

```html
<!DOCTYPE html>
<html lang="es">
<head>
<meta charset="utf-8">
<title>ULMIRA – Tarjeta de presentación</title>
<link rel="stylesheet" href="https://fonts.googleapis.com/css2?family=Open+Sans:wght@400;600;700&display=swap">
<style>
  :root {
    --red: #b3121f;
    --red-dark: #7a0610;
    --red-light: #f06b7d;
    --ink: #1c1c1c;
    --paper: #ffffff;
    --card-black: #161616;
    --grey: #555555;
    --stage: #e9e7e5;
  }
  * { box-sizing: border-box; margin: 0; padding: 0; }
  html, body { width: 1200px; height: 844px; overflow: hidden; }
  body {
    background: var(--stage);
    font-family: "Open Sans", Arial, sans-serif;
    position: relative;
  }
  .card {
    position: absolute;
    top: 272px;
    width: 510px;
    height: 300px;
    overflow: hidden;
    box-shadow: 0 6px 18px rgba(0,0,0,.18);
  }
  .card--front { left: 70px; background: var(--paper); color: var(--ink); }
  .card--back { left: 620px; background: var(--card-black); color: #fff; }
  .card__bands { position: absolute; inset: 0; width: 100%; height: 100%; }

  .brand { position: absolute; }
  .brand__name {
    font-weight: 400;
    letter-spacing: 12px;
    line-height: 1;
  }
  .brand__rule { height: 1px; margin: 8px 0 6px; }
  .brand__tagline {
    font-size: 11px;
    letter-spacing: 4.2px;
    text-transform: uppercase;
  }

  .card--front .brand { left: 40px; top: 72px; width: 250px; }
  .card--front .brand__name { font-size: 40px; color: var(--ink); }
  .card--front .brand__rule { background: var(--red); }
  .card--front .brand__tagline { color: var(--red); }
  .brand__mark {
    display: block;
    width: 14px; height: 14px;
    background: var(--red);
    margin-bottom: 12px;
  }

  .divider { position: absolute; left: 40px; height: 1px; background: var(--red); }
  .divider--top { top: 178px; width: 330px; }
  .divider--bottom { top: 240px; width: 300px; }

  .person { position: absolute; left: 40px; top: 182px; }
  .person__name { font-size: 17px; font-weight: 700; color: var(--red); line-height: 1.2; }
  .person__role { font-size: 12px; color: var(--grey); }

  .contact { position: absolute; list-style: none; font-size: 12.5px; color: var(--grey); }
  .contact li { display: flex; align-items: center; gap: 6px; height: 20px; }
  .contact--main { left: 40px; top: 246px; }
  .contact--online { left: 195px; top: 180px; }
  .icon { width: 11px; height: 11px; flex: none; }

  .card--back .brand { right: 52px; top: 108px; width: 230px; text-align: left; }
  .card--back .brand__name { font-size: 38px; color: #fff; }
  .card--back .brand__rule { background: #ccc; }
  .card--back .brand__tagline { color: #ddd; font-size: 10.5px; }
</style>
</head>
<body>

<article class="card card--front">
  <svg class="card__bands" viewBox="0 0 510 300" aria-hidden="true">
    <defs>
      <linearGradient id="bandFront" x1="0" y1="0" x2="1" y2="1">
        <stop offset="0" stop-color="var(--red-dark)"/>
        <stop offset=".5" stop-color="var(--red)"/>
        <stop offset="1" stop-color="var(--red-dark)"/>
      </linearGradient>
    </defs>
    <polygon points="470,0 510,0 510,300 430,300" fill="url(#bandFront)"/>
    <polygon points="445,0 460,0 415,300 400,300" fill="var(--red-light)"/>
  </svg>

  <div class="brand">
    <span class="brand__mark"></span>
    <div class="brand__name">ULMIRA</div>
    <div class="brand__rule"></div>
    <div class="brand__tagline">Arquitectura Técnica</div>
  </div>

  <div class="divider divider--top"></div>
  <div class="person">
    <div class="person__name">Tomás Reyes</div>
    <div class="person__role">Managing Director</div>
  </div>

  <ul class="contact contact--online">
    <li>
      <svg class="icon" viewBox="0 0 12 12"><rect x="1" y="2.5" width="10" height="7" fill="var(--red)"/><path d="M1 2.5l5 4 5-4" stroke="#fff" fill="none"/></svg>
      info@ulmira-example.com
    </li>
    <li>
      <svg class="icon" viewBox="0 0 12 12"><circle cx="6" cy="6" r="5.5" fill="var(--red)"/></svg>
      @ulmiraAT
    </li>
  </ul>

  <div class="divider divider--bottom"></div>
  <ul class="contact contact--main">
    <li>
      <svg class="icon" viewBox="0 0 12 12"><path d="M2.5 1l2 2-1 1.5c.6 1.4 1.6 2.4 3 3l1.5-1 2 2-1.5 2C5 11 1 7 .5 2.5z" fill="var(--red)"/></svg>
      (044)-555-0182
    </li>
    <li>
      <svg class="icon" viewBox="0 0 12 12"><circle cx="6" cy="6" r="5" fill="none" stroke="var(--red)" stroke-width="1.5"/><path d="M1 6h10M6 1c-2.5 3-2.5 7 0 10M6 1c2.5 3 2.5 7 0 10" stroke="var(--red)" fill="none"/></svg>
      www.ulmira-example.com
    </li>
  </ul>
</article>

<article class="card card--back">
  <svg class="card__bands" viewBox="0 0 510 300" aria-hidden="true">
    <defs>
      <linearGradient id="bandBack" x1="0" y1="0" x2="1" y2="1">
        <stop offset="0" stop-color="var(--red-light)"/>
        <stop offset=".45" stop-color="var(--red)"/>
        <stop offset="1" stop-color="var(--red-dark)"/>
      </linearGradient>
    </defs>
    <polygon points="0,20 0,60 210,240 250,240" fill="url(#bandBack)"/>
    <polygon points="0,0 0,10 260,230 270,230" fill="var(--red-light)"/>
    <polygon points="0,255 250,262 250,272 0,272" fill="var(--red-light)"/>
  </svg>

  <div class="brand">
    <div class="brand__name">ULMIRA</div>
    <div class="brand__rule"></div>
    <div class="brand__tagline">Arquitectura Técnica</div>
  </div>
</article>

</body>
</html>
```